Summer Sunglass offer

Need a poster design for a spring / summer campaign. We are an opticians with good footfall. The design needs to be eye catching and aimed at 40 year old plus. The offer is Up to 50% off sunglass offer, t&c apply. (I have attached our last year campaign)
Also need a 2 sided A5 leaflet design (see attached)
I've uploaded a copy of our logo

A5 leaflet should read:

Grab a bargain on two great looks this summer Upto 50% off sunglasses
Look great and stay safe in the sun this summer

We want you to look great, feel fantastic and most of all stay safe in the sun this summer. That’s why we’re offering you 50% off prescription sunglasses with every complete pair of glasses you buy this summer or 25% off for prescription sunglasses with no other purchase.
Find you new summer looks from our gorgeous collection of frames in store. It matters to us that you look great in your new glasses as much as how well you see through them, so we’ll be on hand to help you find frames that suit you best.
What new looks will you go for? Smart or sassy? Formal or Fun? Whatever you’re in the mood for, you’ll find it in our collections this summer.
Call in today to find your new looks, and remember to bring your prescription if you don’t need an eye test.

Target Market(s)

40 + year old

Industry/Entity Type

Optician

Colors

Designer to choose colors to be used in the design.

Requirements
Must have
• Images, preferably a male and Female image

```html
<!DOCTYPE html>
<html lang="en">
<head>
<meta charset="utf-8">
<title>Sunglass Offer Poster</title>
<link href="https://fonts.googleapis.com/css2?family=Allura&family=Oswald:wght@700&family=Roboto:wght@400;700&display=swap" rel="stylesheet">
<style>
  :root {
    --ink: #000000;
    --paper: #ffffff;
    --sky-blue: #4aa3df;
    --deep-blue: #1f5fa8;
    --steel: #9fb3c2;
    --lens-sky: #b9c9d4;
    --asphalt-light: #7a7a7a;
    --asphalt-mid: #555555;
    --asphalt-dark: #1c1c1c;
    --brand-red: #d2232a;
  }
  * { margin: 0; padding: 0; box-sizing: border-box; }
  html, body { width: 849px; height: 1200px; overflow: hidden; background: var(--ink); }
  .poster {
    position: relative;
    width: 849px;
    height: 1200px;
    background: var(--ink);
    font-family: "Roboto", Arial, sans-serif;
    color: var(--paper);
    overflow: hidden;
  }
  .hero-photo {
    position: absolute;
    left: 0; top: 0;
    width: 849px; height: 640px;
    background:
      linear-gradient(180deg,
        var(--lens-sky) 0%,
        #8e9ca6 16%,
        var(--asphalt-light) 30%,
        var(--asphalt-mid) 48%,
        var(--asphalt-dark) 72%,
        var(--ink) 100%);
  }
  .offer-intro {
    position: absolute;
    top: 455px; left: 0; width: 100%;
    text-align: center;
    font-family: "Allura", cursive;
    font-size: 92px;
    line-height: 1;
  }
  .offer-intro .percent { color: var(--sky-blue); font-size: 150px; }
  .offer-headline {
    position: absolute;
    top: 545px; left: 0; width: 100%;
    text-align: center;
    font-family: "Oswald", sans-serif;
    font-weight: 700;
    font-size: 195px;
    line-height: 1.05;
    letter-spacing: 2px;
    transform: scaleX(0.8);
    background: linear-gradient(180deg, #e8eef2 0%, var(--steel) 40%, #52616c 70%, #c7d2da 100%);
    -webkit-background-clip: text;
    background-clip: text;
    color: transparent;
  }
  .offer-tail {
    position: absolute;
    top: 725px; left: 0; width: 100%;
    text-align: center;
    font-family: "Allura", cursive;
    font-size: 100px;
    line-height: 1;
    padding-left: 270px;
  }
  .tagline {
    position: absolute;
    top: 876px; left: 0; width: 100%;
    text-align: center;
    font-weight: 700;
    font-size: 19px;
    letter-spacing: 0.3px;
  }
  .brand-box {
    position: absolute;
    top: 910px; left: 262px;
    width: 325px; height: 96px;
    background: var(--paper);
    display: flex;
    align-items: center;
    gap: 16px;
    padding-left: 22px;
  }
  .brand-dot { width: 62px; height: 62px; border-radius: 50%; background: var(--deep-blue); flex: none; }
  .brand-name {
    font-weight: 700;
    font-size: 27px;
    line-height: 1.05;
    color: var(--deep-blue);
    letter-spacing: 0.5px;
  }
  .website {
    position: absolute;
    top: 1024px; left: 0; width: 100%;
    text-align: center;
    font-weight: 700;
    font-size: 28px;
    color: var(--sky-blue);
  }
  .stockists {
    position: absolute;
    left: 0; bottom: 0;
    width: 849px; height: 68px;
    background: var(--paper);
    display: flex;
    align-items: center;
    justify-content: space-around;
    padding: 0 12px;
  }
  .stockist { font-weight: 700; font-size: 15px; color: var(--ink); letter-spacing: 0.5px; text-transform: uppercase; }
  .stockist.accent { color: var(--brand-red); }
</style>
</head>
<body>
<main class="poster">
  <div class="hero-photo" role="img" aria-label="Photo of aviator sunglasses resting on textured grey asphalt, lenses reflecting a lake and sky, fading to black"></div>

  <p class="offer-intro">Up to <span class="percent">50%</span> off</p>
  <h1 class="offer-headline">SUNGLASS</h1>
  <p class="offer-tail">offer</p>

  <p class="tagline">LOOK GREAT AND STAY SAFE IN THE SUN THIS SEASON</p>

  <div class="brand-box">
    <span class="brand-dot"></span>
    <span class="brand-name">BRAMLEY<br>EYECARE CENTRE</span>
  </div>

  <p class="website">bramleyeyecare.co.uk</p>

  <footer class="stockists">
    <span class="stockist">Hartwell Moore</span>
    <span class="stockist">Linea</span>
    <span class="stockist">Pebble Frames</span>
    <span class="stockist">Vela Rossi</span>
    <span class="stockist">Nora Bay</span>
    <span class="stockist accent">Corsa</span>
  </footer>
</main>
</body>
</html>
```